Very new and innovative Web design for Property managers of Vacation rentals

We are looking for a new website design for travel agencies and property managers specialised on vacation rentals business, holiday villas and apartments.

The end users of this website are travellers who are looking for a vacation home for their next holiday: this is the reason why the website must be easy to use, attractive, professional, possibly elegant and focused on get new reservations.

This is a draft of our current website: https://intro3.kelumsito.com/
Please consider that we would like to have proposals with a totally different and innovative layout, surprise us!

These are the pages of the website:
• Homepage: feel free to redesign all the homepage as you wish, surprise us with something very new! Please consider that Property manager/Travel agencies usually want to have the opportunity to put in evidence groups of houses with specific characteristics (eg. villas with private swimming pool, apartment in big/small towns, villas with air co, etc…), destinations and tourist areas, and sometimes experiences or activities (please consider that the website layout must be suitable even if some of the previous sections are not used).
• Search page: we’d like to organise the results of the search page in three different ways:
o Grid
o Map
o List
• Property page: to illustrate the characteristics, descriptions, images, …. of the property. It is very important to put in evidence images of the property and to maintain the booking form (and the other call to action bottom – eg. whatsapp) always visible
• Custom pages: static pages composed usually by text, images and call to actions
• Contact us (general form)
• Info request (specific of a property form)
• Booking process
• Blog, organised in four pages:
o Home Page – introduction to the blog
o List of articles
o Single article
o Site Map (presentation of categories and sub-categories)

If possible, we’d prefer to receive the material in Adobe XD or similar so that we can obtain the three versions:
- smartphone
- tablet
- desktop

The website will be then developed in Bootstrap: as a result we’ll need the icons in SVG format (or the library used)

In attachment you can find the map of the website pages

```html
<!DOCTYPE html>
<html lang="en"><head><meta charset="utf-8"><title>Contact Us – Casavista</title>
<link href="https://fonts.googleapis.com/css2?family=Oswald:wght@300;400;500&family=Poppins:ital,wght@0,400;0,500;0,600;1,400&display=swap" rel="stylesheet">
<style>
:root{--green:#0eb07b;--mint:#27d69a;--ink:#222;--muted:#555;--line:#9a9a9a;--dark:#1e1c1d;--white:#fff}
*{margin:0;padding:0;box-sizing:border-box}
html,body{width:759px;height:1200px;overflow:hidden;background:var(--white);font-family:'Poppins',sans-serif;color:var(--ink)}
.abs{position:absolute}
.hero{left:0;top:0;width:759px;height:153px;background:linear-gradient(90deg,#2c3236,#5a5548 40%,#3b4a4c 70%,#5d5a4e)}
.logo{font:500 15px 'Poppins',sans-serif;letter-spacing:1px;color:var(--white);display:flex;align-items:center;gap:6px}
.logo i{width:14px;height:14px;background:var(--green);display:inline-block}
.topbar{font-size:7.5px;color:var(--white);letter-spacing:.5px}
.lang{left:632px;top:6px;width:68px;height:22px;background:var(--mint);color:var(--white);font-size:6.5px;display:flex;align-items:center;justify-content:center;gap:4px}
.nav{top:44px;font-size:9px;font-weight:500;letter-spacing:.8px;color:var(--white)}
.hero-title{top:92px;width:759px;text-align:center;font:500 25px 'Oswald',sans-serif;color:var(--white);letter-spacing:-.5px}
.crumb{left:59px;top:175px;font-size:7.5px;color:var(--muted)}
.crumb b{font-weight:400;color:var(--ink)}
h1{left:58px;top:213px;font:300 25px 'Oswald',sans-serif}
.intro{left:59px;top:248px;width:430px;font-size:8.5px;line-height:12.5px;color:var(--muted)}
.org{left:59px;top:296px;font:400 13px 'Oswald',sans-serif}
.info{left:59px;font-size:8px;line-height:10px;display:flex;gap:6px}
.info svg{flex:none;margin-top:1px}
.field{border:1px solid var(--line);font-size:6.5px;color:#555;padding:6px 7px}
.check{left:309px;top:437px;display:flex;gap:6px;font-size:7.5px;font-style:italic;color:#444;align-items:center}
.check span{width:9px;height:9px;border:1px solid #bbb}
.captcha{left:308px;top:456px;width:97px;height:24px;border:1px solid #ddd;background:#f9f9f9;font-size:4.5px;display:flex;align-items:center;gap:4px;padding-left:4px}
.captcha span{width:9px;height:9px;border:1px solid #aaa;background:var(--white)}
.send{left:309px;top:491px;width:56px;height:23px;background:var(--green);color:var(--white);font-size:7px;display:flex;align-items:center;justify-content:center}
.map{left:0;top:547px;width:759px;height:264px;background:linear-gradient(135deg,#eceff1,#e3e6ea 60%,#dde4ee)}
.footer{left:0;top:811px;width:759px;height:389px;background:var(--dark)}
.fh{font-size:9.5px;font-weight:500;letter-spacing:1px;color:var(--mint)}
.fl{font-size:8px;letter-spacing:.8px;color:var(--white)}
.post{display:flex;gap:7px;width:200px}
.post .ph{width:44px;height:38px;flex:none;background:linear-gradient(#6d8a6a,#3f8fc0)}
.post p{font-size:7.5px;font-weight:600;color:var(--mint);line-height:9.5px}
.post small{display:block;font-size:7.5px;color:var(--white);margin-top:9px;font-weight:400}
.cblock{display:flex;gap:8px;align-items:center}
.cblock b{display:block;font-size:9px;color:var(--mint);letter-spacing:1px}
.cblock span{font-size:9px;color:var(--white);letter-spacing:1px}
.vline{width:1px;background:#3a3839}
</style></head><body>
<div class="abs hero" role="img" aria-label="Photo of a canal-side shopping arcade with visitors"></div>
<div class="abs logo" style="left:60px;top:27px"><i></i>Casavista</div>
<div class="abs topbar" style="left:516px;top:11px">⚲ Login</div>
<div class="abs topbar" style="left:565px;top:11px">♥ Wish List (0)</div>
<div class="abs lang"><span style="width:8px;height:6px;background:#fff;display:inline-block"></span>Language ▾</div>
<div class="abs nav" style="left:340px">Last Minute</div>
<div class="abs nav" style="left:431px">Special Offers</div>
<div class="abs nav" style="left:535px">Experience</div>
<div class="abs nav" style="left:626px">Contact Us</div>
<div class="abs hero-title">CONTACT US</div>

<div class="abs crumb">Home Page &nbsp;/&nbsp; <b>Contact Us</b></div>
<h1 class="abs">Contact Us</h1>
<p class="abs intro">Use this form to contact us regarding any topics other than specific property requests which should be done using the form on the property detail pages.</p>

<div class="abs org">Casavista Rentals</div>
<div class="abs info" style="top:329px"><svg width="6" height="8" viewBox="0 0 6 8"><path d="M3 0a3 3 0 0 1 3 3c0 2-3 5-3 5S0 5 0 3a3 3 0 0 1 3-3z" fill="#0eb07b"/><circle cx="3" cy="3" r="1" fill="#fff"/></svg><span>Via dei Tigli 7 50100 Valleverde<br>Firenze, Italy</span></div>
<div class="abs info" style="top:362px"><svg width="6" height="8" viewBox="0 0 6 8"><path d="M1 0h2l-1 2 1.5 3 1-.5L6 6.5 4.5 8C2 7 0 4 0 1z" fill="#0eb07b"/></svg><span>Phone: +39 000 1234567</span></div>
<div class="abs info" style="top:386px"><svg width="8" height="8" viewBox="0 0 8 8"><rect x="0" y="1" width="8" height="7" fill="#0eb07b"/><rect x="2" y="3" width="4" height="1" fill="#fff"/><rect x="2" y="5" width="4" height="1" fill="#fff"/></svg><span>Fax: +39 000 7654321</span></div>
<div class="abs info" style="top:410px"><svg width="8" height="8" viewBox="0 0 8 8"><circle cx="4" cy="4" r="3" fill="#0eb07b"/><path d="M4 0v8M0 4h8M1 1l6 6M7 1L1 7" stroke="#0eb07b"/></svg><span>VAT Code: IT00000000000</span></div>

<div class="abs field" style="left:308px;top:300px;width:128px;height:22px">First Name:</div>
<div class="abs field" style="left:440px;top:300px;width:128px;height:22px">Last Name:</div>
<div class="abs field" style="left:571px;top:300px;width:129px;height:22px">Country:</div>
<div class="abs field" style="left:308px;top:327px;width:128px;height:22px">Email:</div>
<div class="abs field" style="left:440px;top:327px;width:128px;height:22px">Confirm Email:</div>
<div class="abs field" style="left:571px;top:327px;width:129px;height:22px">Phone:</div>
<div class="abs field" style="left:308px;top:355px;width:392px;height:69px;padding-top:5px">Message:</div>
<div class="abs check"><span></span>I would like to subscribe to your newsletter.</div>
<div class="abs captcha"><span></span>I'm not a robot</div>
<div class="abs send">SEND</div>

<div class="abs map" role="img" aria-label="Street map around the office location"></div>

<div class="abs footer"></div>
<div class="abs logo" style="left:61px;top:870px"><i></i>Casavista</div>
<div class="abs fl" style="left:60px;top:913px">Subscribe to our Newsletter</div>
<div class="abs" style="left:59px;top:929px;width:133px;height:1px;background:#fff"></div>
<svg class="abs" style="left:206px;top:925px" width="25" height="8" viewBox="0 0 25 8"><path d="M0 4h24M20 1l4 3-4 3" stroke="#27d69a" fill="none"/></svg>
<p class="abs fl" style="left:60px;top:945px;width:200px;line-height:12px">Our range of services is very large, and we are constantly expanding it.</p>
<div class="abs fh" style="left:326px;top:858px">Navigation</div>
<div class="abs fl" style="left:328px;top:884px">Last Minute</div>
<div class="abs fl" style="left:328px;top:906px">Special Offers</div>
<div class="abs fl" style="left:328px;top:928px">Experience</div>
<div class="abs fl" style="left:328px;top:950px">Contact Us</div>
<div class="abs fh" style="left:500px;top:858px">Recent posts</div>
<div class="abs post" style="left:501px;top:885px"><div class="ph" role="img" aria-label="Poolside with sun loungers"></div><p>Which construction tool is better to choose?<small>2 November, 2020</small></p></div>
<div class="abs post" style="left:501px;top:938px"><div class="ph" role="img" aria-label="Games room with a table-tennis table" style="background:linear-gradient(#6b4a30,#5d8cae)"></div><p>Which construction tool is better to choose?<small>2 November, 2020</small></p></div>

<div class="abs vline" style="left:274px;top:1025px;height:75px"></div>
<div class="abs vline" style="left:483px;top:1025px;height:75px"></div>
<div class="abs" style="left:61px;top:1100px;width:640px;height:1px;background:#3a3839"></div>
<div class="abs cblock" style="left:77px;top:1043px"><svg width="20" height="20" viewBox="0 0 20 20"><path d="M3 1h4l-2 5 4 6 3-2 5 5-3 4C7 18 1 10 3 1z" fill="#0eb07b"/></svg><div><b>Call us</b><span>+1 000 555 0199 (USA)</span></div></div>
<div class="abs cblock" style="left:306px;top:1043px"><svg width="26" height="20" viewBox="0 0 26 20"><rect x="1" y="1" width="24" height="18" rx="2" fill="none" stroke="#27d69a" stroke-width="1.5"/><path d="M1 2l12 9 12-9" fill="none" stroke="#27d69a" stroke-width="1.5"/></svg><div><b>Write to us</b><span>hello@casavista.test</span></div></div>
<div class="abs cblock" style="left:521px;top:1040px"><svg width="20" height="27" viewBox="0 0 20 27"><path d="M10 1a9 9 0 0 1 9 9c0 7-9 16-9 16S1 17 1 10a9 9 0 0 1 9-9z" fill="none" stroke="#27d69a" stroke-width="1.5"/><circle cx="10" cy="10" r="3.5" fill="none" stroke="#27d69a" stroke-width="1.5"/></svg><div><b>Office location</b><span>12 Harbor Lane, Lakeside, NY 10000</span></div></div>

<div class="abs fl" style="left:0;width:759px;text-align:center;top:1117px">Privacy Policies &nbsp;/&nbsp; Reservation Policies &nbsp;/&nbsp; Cookie Policy</div>
<div class="abs fl" style="left:0;width:759px;text-align:center;top:1129px">Copyright © 2021 Casavista. All Rights Reserved. <span style="color:var(--mint)">Powered by Casavista</span></div>
<div class="abs" style="left:366px;top:1152px;width:10px;height:10px;border-radius:50%;background:#fff"></div>
<div class="abs" style="left:379px;top:1152px;width:35px;height:9px;background:#4267b2;border-radius:1px;font-size:5px;color:#fff;text-align:center;line-height:9px">Like 66</div>
</body></html>
```